Camp Thornbrook 2021 Magazine Design

We are for someone to design our annual magazine/newsletter. This is a print newsletter that is a total of 20 pages. It will need to be designed in a way that is easy to share with our printers. The designer will need to be someone who is creative and easy to work with.
For those interested in this project we ask that you design 4 to 6 pages for us to view. Once we select the designer we will want the rest created in a two-week time span. For those submitting a bid please include front cover, theme & dates, mission & vision, and Make the Difference.

This link will provide the layout of the newsletter https://files.parcelvault.example/doc/7qzRk2LmVt9XwPa4NbHc6DsYe3FuJg8KoTiW5rQx/edit?share=1.

This link will provide you with the pictures that are needed and a few documents https://files.parcelvault.example/folders/4TpWx8QnRb2ZyLc7MfVd5HsJ?share=1

Details:
20 pages long (including covers)
8.5 x 11

Please message me if you need any further details.

Target Market(s)

Our alumni base. Covers all ages

Requirements
Must have
• Spelled out in document
Nice to have
• Spelled out in document
Should not have
• Spelled out in document

```html
<!DOCTYPE html>
<html lang="en">
<head>
<meta charset="utf-8">
<title>Make the Difference – Camp Thornbrook</title>
<link href="https://fonts.googleapis.com/css2?family=Montserrat:wght@900&family=Outfit:wght@400;600;700&display=swap" rel="stylesheet">
<style>
  :root {
    --orange: #d9762f;
    --navy: #2c3655;
    --peach: #f0a878;
    --mint: #52c794;
    --forest: #237a57;
    --white: #ffffff;
  }
  * { margin: 0; padding: 0; box-sizing: border-box; }
  html, body { width: 927px; height: 1200px; overflow: hidden; background: var(--white); }
  .page {
    position: relative;
    width: 927px;
    height: 1200px;
    overflow: hidden;
    background: var(--white);
    font-family: "Outfit", sans-serif;
  }
  .top-band {
    position: absolute; left: 0; top: 0; width: 100%; height: 48px;
    background: var(--orange);
  }
  .lower-band {
    position: absolute; left: 0; top: 636px; width: 100%; height: 564px;
    background: var(--forest);
  }
  .headline {
    position: absolute; left: 43px; top: 104px; width: 430px;
    font-family: "Montserrat", sans-serif;
    font-weight: 900;
    font-size: 61px;
    line-height: 88px;
    letter-spacing: -2px;
    white-space: nowrap;
    color: var(--navy);
    text-shadow: 3px 3px 0 var(--peach);
  }
  .intro-box {
    position: absolute; left: 42px; top: 303px; width: 428px; height: 410px;
    background: var(--mint);
    padding: 28px 31px 0 33px;
  }
  .intro-box p, .story p {
    color: var(--white);
    font-size: 16.3px;
    line-height: 20px;
    text-align: justify;
    hyphens: auto;
  }
  .intro-box p + p { margin-top: 20px; }
  .feature-photo {
    position: absolute; left: 492px; top: 119px; width: 389px; height: 586px;
    background: linear-gradient(160deg, #7ccf4a 0%, #4e9e32 45%, #3a6f35 75%, #6d7f8c 100%);
  }
  .camp-mark {
    position: absolute; left: 10px; bottom: 18px;
    display: flex; align-items: center; gap: 6px;
    font-family: "Outfit", sans-serif;
    font-weight: 700;
    font-size: 13px;
    color: var(--white);
  }
  .camp-mark .dot {
    width: 12px; height: 12px; border-radius: 50%;
    background: var(--orange);
  }
  .story {
    position: absolute; left: 70px; top: 730px; width: 788px;
  }
  .story p + p { margin-top: 20px; }
  .tab-left {
    position: absolute; left: 0; top: 1145px; width: 76px; height: 24px;
    background: var(--white);
  }
  .tab-right {
    position: absolute; left: 850px; top: 1145px; width: 77px; height: 24px;
    background: var(--white);
    font-family: "Outfit", sans-serif;
    font-weight: 700;
    font-size: 20px;
    line-height: 24px;
    color: var(--mint);
    text-align: center;
  }
</style>
</head>
<body>
<div class="page">
  <div class="top-band"></div>
  <div class="lower-band"></div>

  <h1 class="headline">MAKE THE<br>DIFFERENCE</h1>

  <div class="intro-box">
    <p>To say that 2020 has been a challenging year is a huge understatement! March 2020 is a month none of us will soon forget.  Just as we were getting ready to ramp up for the summer, things began to shut down all around us.  At first we hoped it would just be a few weeks only impacting our spring retreats, but as the spring progressed, it soon became evident our 2020 summer was being threatened.</p>
    <p>In late May, we made the difficult decision to cancel all summer events.  For the first time in 73 years, there would be no summer camp at Thornbrook.  Our summer programming is at the heart of what we do and who we are.  From the very beginning, Thornbrook’s main mission has been to share Christ through the summer camp program.</p>
  </div>

  <div class="feature-photo" role="img" aria-label="Campaign poster photo: a counselor hugging two young campers outdoors among green trees, with the title Make the Difference, July 13th – 17th">
    <div class="camp-mark"><span class="dot"></span>Camp Thornbrook</div>
  </div>

  <div class="story">
    <p>After dealing with the emotional aspect of not having camp this summer, we had to look at the reality of the financial impact canceling the summer would have on Thornbrook.  Over 50% of our annual revenue comes from our summer programming and summer rentals.  We also had to take into account the loss of our spring rentals and the possibility of fall rentals canceling.  While we were confident God would provide for Thornbrook, as He always has, we weren’t sure how this would take place.</p>
    <p>We determined that even with drastically cutting expenses, we would need an additional $50,000 to make up for the lost revenue. In late June, we received a phone call from one of our long-time Thornbrook families who was interested in helping us through this difficult time.  They generously pledged $10,000 as a matching gift to help motivate the Thornbrook family to give as well.  In early July, we announced the “Make the Difference” fundraising campaign. Our initial goal was to raise $10,000 in one week to receive the matching gift with the hope of substantially reducing the $50,000 deficit.</p>
    <p>The Thornbrook family showed their love and dedication through their extraordinary generosity.  By the end of Monday, the first day of the campaign, we had exceeded our initial goal of $10,000 ensuring the matching gift.  By the end of the week, over $64,000 was raised!</p>
    <p>While 2020 has not been the year we had hoped for, it has been a year in which Thornbrook has been blessed beyond expectations!</p>
  </div>

  <div class="tab-left"></div>
  <div class="tab-right">3</div>
</div>
</body>
</html>
```